Exclusive beauty salon needs a price list or services booklet

I need a new very attractive flyer for my beauty salon, containing information on the different services and their prices.
In attachment you can find a pdf of the "old" one, but I'd love to have a beautifully designed new one!
I'd love to have a booklet in format 148 x 148 mm, or in US format, containing 12 or 16 pages, but if you can offer other nice looking designs they are welcome!
The services that need to come in the booklet with their prices can all be found on my website: www.atelierverano.be, starting with
Gelaatsverzorging
Wimperverlenging
Suikerontharing
Wimperlifting
Permanente Make Up
Airbrush Tanning

Target Market(s)

woman from 20 to 89 years old

Industry/Entity Type

Beauty Salon

Font styles to use
Sans Serif

Colors

Designer to choose colors to be used in the design.

Requirements
Must have
• a classy nice look, it must contain details about the services from my beauty salon and their prices, and nice pictures.
• The Names, prices and explanations of the services can easily be found on my website: www.atelierverano.be
Nice to have
• In attachment you can find the "old" price list in pdf, what I need now is a "new booklet" with the new logo and updated services price list.
• I need a very nice and attractive looking booklet, classy chique, Paris chique, looking very expensive.
Should not have
• Not too much colors, not too curly, but still feminine

```html
<!DOCTYPE html>
<html lang="nl">
<head>
<meta charset="utf-8">
<title>Atelier Verano – Brochure</title>
<link href="https://fonts.googleapis.com/css2?family=Source+Sans+3:ital,wght@0,400;0,600;1,400&display=swap" rel="stylesheet">
<style>
  :root{
    --backdrop:#5f5f5f;
    --paper:#ffffff;
    --stone:#a3a7aa;
    --teal:#5bbfcc;
    --teal-veil:rgba(120,200,212,.72);
    --plum:#4a1a3c;
    --body:#9a9a9a;
  }
  *{box-sizing:border-box;margin:0;padding:0}
  html,body{width:1200px;height:871px;overflow:hidden;background:var(--backdrop)}
  body{position:relative;font-family:"Source Sans 3",sans-serif}
  .page{position:absolute}
  .page--white{background:var(--paper)}
  .page--stone{background:var(--stone)}
  .inset{position:absolute}
  .photo{position:absolute}

  /* Cover spread */
  .cover{left:23px;top:14px;width:571px;height:407px}
  .brand{position:absolute;left:34px;top:36px;font-size:9px;letter-spacing:.12em;color:#444;z-index:2}
  .arrow{position:absolute;width:13px;height:25px}
  .title-box{position:absolute;left:209px;top:159px;width:151px;height:91px;background:var(--teal-veil);
    color:#fff;font-size:17px;line-height:1.4;display:flex;flex-direction:column;align-items:center;justify-content:center;text-align:center}

  /* Intro spread */
  .intro{left:612px;top:14px;width:570px;height:407px}
  .intro .inset{left:23px;top:23px;width:524px;height:361px;background:var(--stone)}
  .intro-frame{position:absolute;left:115px;top:79px;width:298px;height:206px;border:1px solid #fff;padding:24px 15px 0 15px;
    color:#fff;font-style:italic;font-size:11.4px;line-height:1.33}
  .intro-frame p+p{margin-top:7px}
  .price-tag{position:absolute;left:0;right:0;top:312px;text-align:center;color:#fff;font-size:13.5px}

  /* Tanning spreads */
  .tan-a{left:23px;top:441px;width:571px;height:405px}
  .tan-b{left:612px;top:441px;width:570px;height:405px}
  .tan-a .inset,.tan-b .inset{left:23px;top:22px;width:524px;height:361px;background:var(--paper)}
  .copy{position:absolute;color:var(--body);font-style:italic;font-size:8.3px;line-height:1.45;text-align:justify}
  .copy h2{font-style:normal;font-weight:400;color:var(--teal);font-size:12.8px;margin:0 0 7px}
  .copy p{margin-bottom:3px}
  .copy h2:not(:first-child){margin-top:11px}
  .tan-a .copy{left:277px;top:20px;width:226px}
  .tan-b .copy{left:21px;top:20px;width:226px}
  .service-price{position:absolute;left:21px;top:322px;width:244px;display:flex;justify-content:space-between;
    color:var(--body);font-style:italic;font-size:10.5px}
  .service-price span:last-child{color:var(--teal)}
</style>
</head>
<body>

<section class="page page--white cover">
  <div class="brand">ATELIER VERANO</div>
  <div class="photo" role="img" aria-label="Zijaanzicht van een oog vóór de wimperlifting" style="left:27px;top:23px;width:188px;height:162px;background:radial-gradient(ellipse 70% 80% at 35% 70%,#d8ab92 0%,#e9cbb8 45%,#f6ebe4 100%)"></div>
  <div class="photo" role="img" aria-label="Zijaanzicht van een oog na de wimperlifting" style="left:319px;top:23px;width:228px;height:162px;background:radial-gradient(ellipse 60% 85% at 30% 60%,#d6a68c 0%,#eacdbb 45%,#f8f1ec 100%)"></div>
  <div class="photo" role="img" aria-label="Vooraanzicht van een oog vóór de wimperlifting" style="left:27px;top:200px;width:246px;height:184px;background:radial-gradient(ellipse 75% 55% at 55% 55%,#b9a79a 0%,#e5cbbb 40%,#f1e0d5 75%,#e9d2c3 100%)"></div>
  <div class="photo" role="img" aria-label="Vooraanzicht van een oog na de wimperlifting" style="left:319px;top:200px;width:228px;height:184px;background:radial-gradient(ellipse 75% 55% at 50% 55%,#a99a90 0%,#e2c7b6 40%,#f1e1d6 75%,#ead4c5 100%)"></div>
  <svg class="arrow" style="left:292px;top:62px" viewBox="0 0 13 25"><polygon points="0,0 13,12.5 0,25" fill="var(--plum)"/></svg>
  <svg class="arrow" style="left:292px;top:292px" viewBox="0 0 13 25"><polygon points="0,0 13,12.5 0,25" fill="var(--plum)"/></svg>
  <div class="title-box"><span>Wimperlifting</span><span>Lumi Lift</span></div>
</section>

<section class="page page--white intro">
  <div class="inset">
    <div class="intro-frame">
      <p>Het hebben van mooie, lange en volumineuze wimpers staat hoog op het verlanglijstje van vele vrouwen. Het liefst heeft men de wimpers mooi gelift voor een open blik die de ogen optisch groter maakt. Niet voor niets is mascara één van de best verkochte make-upproducten.</p>
      <p>De nieuwe en revolutionaire Lumi Lift-methode zorgt echter na slechts 1 behandeling van 60 minuten, gedurende minimaal 6 weken voor Lange, Volumineuze en geLifte wimpers. Dit alles, zonder dat daar een wimperkrultang of dikke lagen mascara aan te pas hoeven te komen!</p>
    </div>
    <div class="price-tag">Wimperlifting €65</div>
  </div>
</section>

<section class="page page--stone tan-a">
  <div class="inset">
    <div class="photo" role="img" aria-label="Gebruinde heup en dij met zwart bikinibroekje" style="left:0;top:0;width:252px;height:361px;background:radial-gradient(ellipse 55% 75% at 55% 55%,#a8643c 0%,#c48155 40%,#dfae8c 70%,#f6efea 100%)"></div>
    <div class="copy">
      <h2>Airbrush Tanning</h2>
      <p>Altijd al gedroomd van een natuurlijk mooi én egaal bruin kleurtje? En dit zonder te puffen in de zon of te knoeien met zelfbruiner? Ik stel u graag de spraycabine van Solara voor!</p>
      <h2>De Voorbereiding</h2>
      <p>De dag van de afspraak kan je beter geen vette of oliehoudende producten op het lichaam aanbrengen. Een goede scrubbeurt (op waterbasis, zonder olie !!) zal ervoor zorgen dat de kleur mooi egaal en gelijkmatig verdeeld wordt en belangrijker nog, dat je huid veel langer bruin zal blijven. De loszittende dode huidcellen worden verwijderd bij het scrubben. Degene die nog vast zitten zullen nog veel langer op hun plaats blijven. Opgelet : indien je zelf de scrub uitvoert, zorg ervoor dat je geen stukken vergeet !</p>
      <p>Trek donkere loszittende kledij aan. Op lichte kledij kan de gekleurde component licht kleur afgeven. Dit laat zich volledig verwijderen in de was. De kledij mag niet spannen en vooral geen wrijving op de huid geven. De component die de uiteindelijke kleur moet geven werkt gedurende ongeveer 12 uur verder. Op plaatsen waar de kledij op de huid schuurt kan het product vroegtijdig weggewreven worden en dus lichtere strepen geven.</p>
      <p>Het product laat geen vlekken na op de kledij. Alleen op de materialen van zeer fijne lingerie kan het het eventueel inwerken.</p>
    </div>
  </div>
</section>

<section class="page page--stone tan-b">
  <div class="inset">
    <div class="copy">
      <h2>De Airbrush Tanning Zelf</h2>
      <p>Je huid wordt ingespoten met het product. Je ziet onmiddellijk het resultaat. Eventueel wordt in verschillende lagen gespoten zodat je zeker niet te bruin kan worden. Het inspuiten van het volledig lichaam duurt ongeveer 10 minuten. Daarna moet je alvorens de kleren aan te trekken nog een kwartiertje het product laten indrogen. Je verlaat het instituut met een mooie, gezonde bruine kleur.</p>
      <h2>De Nazorg</h2>
      <p>Gedurende de eerste 8 uren na de airbrush tanning kan je best voorkomen om hevig te zweten. Dus best geen sport of andere zware inspanningen. Je mag niet douchen ! Tijdens deze eerste 8 uren kan het product een lichte kleur afgeven op kledij of lakens. Deze verdwijnt zonder probleem in de was. Na 8 uur mag je douchen. De tijdelijke kleurcomponent spoelt volledig weg. Ondertussen heeft je huid een mooie bruine kleur gekregen. Hoe beter je je huid hydrateert hoe langer je de kleur kan behouden. Je kleur blijft gemiddeld tussen de 7 dagen en 10 dagen naargelang je huidtype. Daarna begint de kleur te vervagen.</p>
    </div>
    <div class="service-price"><span>Airbrush tanning van het volledige lichaam</span><span>€29</span></div>
    <div class="photo" role="img" aria-label="Portret van een vrouw, half lichte en half gebruinde huid" style="left:272px;top:0;width:252px;height:361px;background:linear-gradient(90deg,#e9e9ea 0%,#efdfd3 14%,#ecd3c2 49%,#e2a57c 50%,#d99569 86%,#e6e4e2 100%)"></div>
  </div>
</section>

</body>
</html>
```